New Business Card Design Project

Need a design that will create an impact / strong impression towards our clients for our business. We are in the lighting business and we do lighting retrofits for large commercial to industrial clientele.

Target Market(s)

Lighting Industry

Industry/Entity Type

Business

Font styles to use
Other font styles liked:
• we would like to use the font on our logo, not sure what it is though..

Requirements
Must have
• Our logo.
Nice to have
• We are open to suggestions that have to do with lighting.

```html
<!DOCTYPE html>
<html lang="en">
<head>
<meta charset="utf-8">
<title>Lumacore Retrofit Partners – Business Card</title>
<link rel="stylesheet" href="https://fonts.googleapis.com/css2?family=Source+Sans+3:wght@400;600;700&display=swap">
<style>
  :root {
    --backdrop: #2a2a2a;
    --card: #f4f4f2;
    --green-bright: #2a9c3c;
    --green-deep: #14521f;
    --ink: #2c2c2c;
    --rule: #d6d6d2;
  }
  * { box-sizing: border-box; margin: 0; padding: 0; }
  html, body {
    width: 1200px; height: 900px; overflow: hidden;
    background: var(--backdrop);
    font-family: "Source Sans 3", "Myriad Pro", Arial, sans-serif;
  }
  .stage {
    width: 1200px; height: 900px;
    display: flex; align-items: center; justify-content: center; gap: 50px;
  }
  .card {
    width: 520px; height: 300px;
    background: var(--card);
    border-radius: 26px;
    position: relative;
    box-shadow: 0 6px 18px rgba(0,0,0,.35);
  }
  /* Back: contact side */
  .card--back { display: flex; align-items: center; }
  .brand-area {
    width: 240px; height: 100%;
    display: flex; align-items: center; justify-content: center; gap: 10px;
  }
  .brand-square { width: 22px; height: 22px; background: var(--green-deep); }
  .brand-name {
    font-weight: 700; font-size: 22px; color: var(--green-deep); line-height: 1.1;
  }
  .contact {
    height: 190px; padding-left: 22px;
    border-left: 1px solid var(--rule);
    color: var(--ink);
  }
  .contact__name { font-size: 24px; font-weight: 600; color: var(--green-bright); line-height: 1; }
  .contact__role { font-size: 15px; margin-top: 3px; }
  .contact__address { font-size: 15px; line-height: 1.25; margin-top: 14px; }
  .contact__lines { list-style: none; margin-top: 14px; font-size: 15px; line-height: 1.35; }
  .contact__lines li { display: flex; align-items: center; gap: 8px; }
  .contact__lines svg { width: 12px; height: 12px; fill: var(--green-bright); flex: none; }
  /* Front: brand side */
  .card--front { display: flex; align-items: center; justify-content: center; }
  .front-brand { display: flex; flex-direction: column; align-items: flex-start; }
  .front-brand__row { display: flex; align-items: center; gap: 14px; }
  .front-brand__square { width: 34px; height: 34px; background: var(--green-deep); }
  .front-brand__name { font-weight: 700; font-size: 40px; color: var(--green-deep); line-height: 1; }
  .front-brand__rule { width: 100%; height: 2px; background: var(--green-bright); margin: 10px 0 6px; }
  .front-brand__tag { font-size: 13px; font-weight: 700; letter-spacing: 1.5px; color: var(--green-deep); text-transform: uppercase; }
</style>
</head>
<body>
<main class="stage">
  <section class="card card--back">
    <div class="brand-area">
      <span class="brand-square"></span>
      <span class="brand-name">Lumacore</span>
    </div>
    <div class="contact">
      <p class="contact__name">Marcus Hale</p>
      <p class="contact__role">Managing Director</p>
      <p class="contact__address">12345, Address Goes Here<br>Country Name, 123456.</p>
      <ul class="contact__lines">
        <li><svg viewBox="0 0 12 12"><path d="M2.5 1l2 2.2-1 1.3c.7 1.5 1.8 2.6 3.3 3.3l1.3-1 2.2 2-1.3 1.9C5 10.4 1.6 7 .6 2.3z"/></svg>044-555 210 873</li>
        <li><svg viewBox="0 0 12 12"><path d="M0 2h12v8H0zM1 3l5 3.5L11 3v-.2H1z"/></svg>hello@lumacore.example</li>
        <li><svg viewBox="0 0 12 12"><path d="M4.5 7.5l3-3M3 6L1.5 7.5a2 2 0 003 3L6 9M9 6l1.5-1.5a2 2 0 00-3-3L6 3" stroke="#2a9c3c" stroke-width="1.5" fill="none"/></svg>www.lumacore.example</li>
      </ul>
    </div>
  </section>
  <section class="card card--front">
    <div class="front-brand">
      <div class="front-brand__row">
        <span class="front-brand__name">Lumacore</span>
        <span class="front-brand__square"></span>
      </div>
      <div class="front-brand__rule"></div>
      <p class="front-brand__tag">Retrofit Partners, LLC.</p>
    </div>
  </section>
</main>
</body>
</html>
```